Design a Brazilian children's Bible calendar for 2017

We need someone to design a children's calendar for 2017 with an animal theme.
The format is 21cm x 15cm and we need the front cover and one page with two months as can be seen in the attached files.
Target Market(s)
Brazilian children
Font styles to use
Sans Serif
Requirements
Must have
- Modern, clean design

```html
<!DOCTYPE html>
<html lang="pt-BR">
<head>
<meta charset="utf-8">
<title>Calendário Infantil 2017</title>
<link rel="stylesheet" href="https://fonts.googleapis.com/css2?family=Quicksand:wght@400;500;700&family=Raleway:wght@700;800&display=swap">
<style>
  :root {
    --canvas: #ffffff;
    --ink-light: #ffffff;
    --sea-panel: #6786ac;
    --sea-accent: #f08c9c;
    --sea-art: #7a97ba;
    --meadow-panel: #b08eae;
    --meadow-accent: #64106f;
    --meadow-art: #bd9fbb;
    --forest-panel: #7dbd4b;
    --forest-accent: #a3181c;
    --forest-art: #8fc962;
  }
  * { box-sizing: border-box; margin: 0; padding: 0; }
  html, body { width: 1200px; height: 480px; overflow: hidden; background: var(--canvas); }
  .spread { position: relative; width: 1200px; height: 480px; }

  .page {
    position: absolute; top: 16px; width: 318px; height: 446px;
    background: var(--panel); overflow: hidden;
    font-family: "Quicksand", sans-serif; color: var(--ink-light);
  }
  .page--sea { left: 54px; --panel: var(--sea-panel); --accent: var(--sea-accent); --art: var(--sea-art); }
  .page--meadow { left: 441px; --panel: var(--meadow-panel); --accent: var(--meadow-accent); --art: var(--meadow-art); }
  .page--forest { left: 822px; --panel: var(--forest-panel); --accent: var(--forest-accent); --art: var(--forest-art); }

  .photo { position: absolute; left: 0; top: 0; width: 318px; height: 192px; }
  .page--sea .photo { background: linear-gradient(180deg, #e3e8ea 0%, #d4dde2 50%, #5f9fc6 72%, #8cb6cf 88%, #5b5650 100%); }
  .page--meadow .photo { background: radial-gradient(circle at 40% 40%, #e9e2d2 0 14%, transparent 22%), linear-gradient(180deg, #8d8a3c 0%, #e5c53c 55%, #d9b52c 100%); }
  .page--forest .photo { background: linear-gradient(180deg, #a9b8c6 0%, #44607e 35%, #2b4058 55%, #3b4a33 72%, #2a3324 100%); }

  .art { position: absolute; border-radius: 10px; background: var(--art); }
  .art--left { left: 30px; top: 218px; width: 92px; height: 52px; }
  .art--right { left: 190px; top: 214px; width: 112px; height: 56px; }
  .page--meadow .art--left { left: 18px; width: 104px; top: 228px; height: 40px; }
  .page--meadow .art--right { left: 194px; width: 110px; top: 228px; height: 40px; }
  .page--meadow .art--top { left: 150px; top: 210px; width: 42px; height: 28px; }

  .year {
    position: absolute; left: 0; width: 318px; top: 248px; text-align: center;
    font-family: "Raleway", sans-serif; font-weight: 800; font-size: 25px; line-height: 1;
    color: var(--accent);
  }
  .tagline {
    position: absolute; left: 0; width: 318px; top: 276px; text-align: center;
    font-family: "Raleway", sans-serif; font-weight: 700; font-size: 9.6px; line-height: 8px;
    color: var(--accent);
  }
  .subline {
    position: absolute; left: 0; width: 318px; top: 294px; text-align: center;
    font-family: "Raleway", sans-serif; font-weight: 700; font-size: 7px; line-height: 1;
    color: var(--accent);
  }

  .month { position: absolute; top: 304px; width: 126px; }
  .month--first { left: 21px; }
  .month--second { left: 165px; }
  .month-name { text-align: center; font-size: 19px; font-weight: 400; line-height: 22px; letter-spacing: 0.2px; }
  .weekdays, .days { display: grid; grid-template-columns: repeat(7, 18px); list-style: none; }
  .weekdays { margin-top: 8px; }
  .weekdays li {
    width: 15px; height: 15px; margin: 0 auto; border-radius: 50%;
    background: var(--ink-light); color: var(--accent);
    font-size: 4.6px; font-weight: 700; line-height: 15px; text-align: center;
  }
  .days { margin-top: 4px; }
  .days li { text-align: center; font-size: 10.5px; font-weight: 500; line-height: 13.6px; }
  .days .s2 { grid-column-start: 2; }
  .days .s3 { grid-column-start: 3; }
  .days .s4 { grid-column-start: 4; }
  .days .s6 { grid-column-start: 6; }
  .days .s7 { grid-column-start: 7; }
</style>
</head>
<body>
<main class="spread">

  <section class="page page--sea">
    <div class="photo" role="img" aria-label="Foto de uma gaivota em pé sobre uma pedra, com o mar ao fundo"></div>
    <div class="art art--left" role="img" aria-label="Ilustração de um barquinho sobre as ondas"></div>
    <div class="art art--right" role="img" aria-label="Ilustração de uma gaivota voando entre nuvens e pássaros"></div>
    <p class="year">2017</p>
    <p class="tagline">Lorem ipsum dolor sit amet czonsectetuer adipiscing<br>elit aenean commodo</p>
    <p class="subline">Lorem Ipsum</p>

    <div class="month month--first">
      <h2 class="month-name">Julho</h2>
      <ul class="weekdays"><li>DOM</li><li>TER</li><li>QUA</li><li>QUI</li><li>QUI</li><li>SEX</li><li>SÁB</li></ul>
      <ol class="days"><li class="s7">1</li><li>2</li><li>3</li><li>4</li><li>5</li><li>6</li><li>7</li><li>8</li><li>9</li><li>10</li><li>11</li><li>12</li><li>13</li><li>14</li><li>15</li><li>16</li><li>17</li><li>18</li><li>19</li><li>20</li><li>21</li><li>22</li><li>23</li><li>24</li><li>25</li><li>26</li><li>27</li><li>28</li><li>29</li><li>30</li><li>31</li></ol>
    </div>
    <div class="month month--second">
      <h2 class="month-name">Agosto</h2>
      <ul class="weekdays"><li>DOM</li><li>TER</li><li>QUA</li><li>QUI</li><li>QUI</li><li>SEX</li><li>SÁB</li></ul>
      <ol class="days"><li class="s3">1</li><li>2</li><li>3</li><li>4</li><li>5</li><li>6</li><li>7</li><li>8</li><li>9</li><li>10</li><li>11</li><li>12</li><li>13</li><li>14</li><li>15</li><li>16</li><li>17</li><li>18</li><li>19</li><li>20</li><li>21</li><li>22</li><li>23</li><li>24</li><li>25</li><li>26</li><li>27</li><li>28</li><li>29</li><li>30</li><li>31</li></ol>
    </div>
  </section>

  <section class="page page--meadow">
    <div class="photo" role="img" aria-label="Foto de uma coruja-das-torres num campo de flores amarelas"></div>
    <div class="art art--left" role="img" aria-label="Ilustração de capim com florzinhas amarelas"></div>
    <div class="art art--top" role="img" aria-label="Ilustração de uma corujinha"></div>
    <div class="art art--right" role="img" aria-label="Ilustração de capim com florzinhas amarelas"></div>
    <p class="year">2017</p>
    <p class="tagline">Lorem ipsum dolor sit amet czonsectetuer adipiscing<br>elit aenean commodo</p>
    <p class="subline">Lorem Ipsum</p>

    <div class="month month--first">
      <h2 class="month-name">Septembro</h2>
      <ul class="weekdays"><li>DOM</li><li>TER</li><li>QUA</li><li>QUI</li><li>QUI</li><li>SEX</li><li>SÁB</li></ul>
      <ol class="days"><li class="s6">1</li><li>2</li><li>3</li><li>4</li><li>5</li><li>6</li><li>7</li><li>8</li><li>9</li><li>10</li><li>11</li><li>12</li><li>13</li><li>14</li><li>15</li><li>16</li><li>17</li><li>18</li><li>19</li><li>20</li><li>21</li><li>22</li><li>23</li><li>24</li><li>25</li><li>26</li><li>27</li><li>28</li><li>29</li><li>30</li></ol>
    </div>
    <div class="month month--second">
      <h2 class="month-name">Outubro</h2>
      <ul class="weekdays"><li>DOM</li><li>TER</li><li>QUA</li><li>QUI</li><li>QUI</li><li>SEX</li><li>SÁB</li></ul>
      <ol class="days"><li>1</li><li>2</li><li>3</li><li>4</li><li>5</li><li>6</li><li>7</li><li>8</li><li>9</li><li>10</li><li>11</li><li>12</li><li>13</li><li>14</li><li>15</li><li>16</li><li>17</li><li>18</li><li>19</li><li>20</li><li>21</li><li>22</li><li>23</li><li>24</li><li>25</li><li>26</li><li>27</li><li>28</li><li>29</li><li>30</li><li>31</li></ol>
    </div>
  </section>

  <section class="page page--forest">
    <div class="photo" role="img" aria-label="Foto de um cervo num campo de mato com montanhas ao fundo"></div>
    <div class="art art--left" role="img" aria-label="Ilustração de pinheiros e uma rena"></div>
    <div class="art art--right" role="img" aria-label="Ilustração de árvore de Natal, presentes, floco de neve e bengalas doces"></div>
    <p class="year">2017</p>
    <p class="tagline">Lorem ipsum dolor sit amet czonsectetuer adipiscing<br>elit aenean commodo</p>
    <p class="subline">Lorem Ipsum</p>

    <div class="month month--first">
      <h2 class="month-name">Novembro</h2>
      <ul class="weekdays"><li>DOM</li><li>TER</li><li>QUA</li><li>QUI</li><li>QUI</li><li>SEX</li><li>SÁB</li></ul>
      <ol class="days"><li class="s4">1</li><li>2</li><li>3</li><li>4</li><li>5</li><li>6</li><li>7</li><li>8</li><li>9</li><li>10</li><li>11</li><li>12</li><li>13</li><li>14</li><li>15</li><li>16</li><li>17</li><li>18</li><li>19</li><li>20</li><li>21</li><li>22</li><li>23</li><li>24</li><li>25</li><li>26</li><li>27</li><li>28</li><li>29</li><li>30</li></ol>
    </div>
    <div class="month month--second">
      <h2 class="month-name">Dezembro</h2>
      <ul class="weekdays"><li>DOM</li><li>TER</li><li>QUA</li><li>QUI</li><li>QUI</li><li>SEX</li><li>SÁB</li></ul>
      <ol class="days"><li class="s6">1</li><li>2</li><li>3</li><li>4</li><li>5</li><li>6</li><li>7</li><li>8</li><li>9</li><li>10</li><li>11</li><li>12</li><li>13</li><li>14</li><li>15</li><li>16</li><li>17</li><li>18</li><li>19</li><li>20</li><li>21</li><li>22</li><li>23</li><li>24</li><li>25</li><li>26</li><li>27</li><li>28</li><li>29</li><li>30</li><li>31</li></ol>
    </div>
  </section>

</main>
</body>
</html>
```